UI/ UX Design for ERP Software

We need a new UX/UI interface for a ERP software for property managers. Our CMMS / ERP solution is made based on responsive design technologies and is coded in PHP.
The overall UX to be similar to Tev Ulna - easy navigation, intuitive menus.

Industry/Entity Type

Property Management

Number of Pages Required

5+ page

Requirements
Must have
• Round dock buttons
Consistent icons across the application
Enough Spacing between buttons/icons/ menu
Consistent Font
Nice to have
• We would like the UX to allow the users to use the application without /minimum training.
Should not have
• we don't want anything that is classic with respect to UX

```html
<!DOCTYPE html>
<html lang="en">
<head>
<meta charset="utf-8">
<title>Estatly – Active Dashboard</title>
<link href="https://fonts.googleapis.com/css2?family=Poppins:wght@400;500;600&family=Open+Sans:wght@400;600&display=swap" rel="stylesheet">
<style>
:root{
  --page-bg:#444444;
  --frame:#ffffff;
  --side-top:#00a8ff;
  --side-bottom:#0080ff;
  --side-line:rgba(255,255,255,.18);
  --accent:#0094ff;
  --ink:#2b2b2b;
  --panel:#f3f3f3;
  --tab-active:#2f2f2f;
  --ring:#b5b5b5;
  --arc:#8cc0ef;
  --arc-light:#b9d8f4;
  --muted:#555;
  --c-sched:#7fb7ea;
  --c-done:#8ae07a;
  --c-future:#ffa14e;
  --c-wo:#3a3a44;
  --c-wodone:#8f8bf0;
  --c-insp:#ef5b86;
  --c-inspdone:#e3cf55;
}
*{box-sizing:border-box;margin:0;padding:0}
html,body{width:1200px;height:1029px;overflow:hidden}
body{background:var(--page-bg);font-family:"Poppins",sans-serif;position:relative}
.app-frame{position:absolute;left:29px;top:34px;width:1142px;height:930px;background:var(--frame);border-radius:3px}
.sidebar{position:absolute;left:34px;top:40px;width:206px;height:916px;border-radius:4px;
  background:linear-gradient(180deg,var(--side-top),var(--side-bottom));overflow:hidden}
.brand{height:63px;display:flex;align-items:center;padding-left:16px;gap:8px;color:#fff;
  font-weight:600;font-size:24px;border-bottom:1px solid var(--side-line)}
.brand-mark{width:14px;height:14px;border-radius:50%;background:#fff}
.nav{list-style:none}
.nav li{height:34.3px;display:flex;align-items:center;padding-left:13px;color:#fff;font-size:12px;
  border-bottom:1px solid var(--side-line);position:relative}
.nav li svg.ico{width:12px;height:12px;margin-right:7px;fill:#fff}
.nav .plus{position:absolute;right:5px;top:12px;width:10px;height:10px}
.collapse-btn{position:absolute;right:0;top:869px;width:27px;height:33px;background:#1a8fe0;
  border-radius:4px 0 0 4px;display:flex;align-items:center;justify-content:center}
.main-title{position:absolute;left:257px;top:56px;display:flex;align-items:center;gap:8px;
  font-size:24px;color:var(--ink);font-weight:400}
.stat{position:absolute;top:54px;height:34px;border:1px solid #d6d6d6;border-radius:2px;
  display:flex;align-items:center;background:#fff}
.stat .ico-cell{width:26px;height:100%;display:flex;align-items:center;justify-content:center;border-right:1px solid #e2e2e2}
.stat .txt{padding-left:6px;font-family:"Open Sans",sans-serif;line-height:1.1}
.stat .lbl{font-size:8px;color:#333}
.stat .val{font-size:13.5px;color:var(--accent)}
.tabs{position:absolute;left:257px;top:103px;width:903px;height:36px;background:var(--accent);
  border-bottom:2px solid #2d2d2d;display:flex;padding-left:6px;font-family:"Open Sans",sans-serif}
.tab{color:#fff;font-size:12px;display:flex;align-items:center;padding:0 14px 4px 11px;border-right:1px solid rgba(0,0,0,.18);gap:4px}
.tab.active{background:var(--tab-active);margin-top:6px;padding-bottom:0}
.tab svg{width:9px;height:9px}
.panel{position:absolute;left:257px;top:141px;width:903px;height:815px;background:var(--panel)}
.range{position:absolute;left:18px;top:17px;display:flex;align-items:center;gap:9px;font-size:17px;color:var(--ink)}
.chart{position:absolute;left:0;top:0}
.date-pill{position:absolute;left:225px;top:309px;width:122px;height:38px;border-radius:19px;
  background:var(--arc);color:#fff;font-size:17px;display:flex;align-items:center;justify-content:center}
.legend{position:absolute;left:618px;top:56px;width:267px;height:261px;background:#fff;padding-top:16px}
.legend li{list-style:none;height:34.3px;display:flex;align-items:center;padding-left:16px;font-size:12px}
.legend .dot{width:18px;height:18px;border-radius:50%;margin-right:12px}
.footer{position:absolute;top:988px;width:1200px;text-align:center;color:#fff;font-family:"Open Sans",sans-serif;font-size:12px}
</style>
</head>
<body>
<svg width="0" height="0" style="position:absolute">
  <symbol id="i-sq" viewBox="0 0 12 12"><rect x="1" y="1" width="10" height="10" rx="2"/></symbol>
  <symbol id="i-user" viewBox="0 0 12 12"><circle cx="6" cy="4" r="3"/><path d="M1 12c0-3 2-5 5-5s5 2 5 5z"/></symbol>
  <symbol id="i-home" viewBox="0 0 12 12"><path d="M6 1l5.5 5H10v5H7.5V8h-3v3H2V6H.5z"/></symbol>
  <symbol id="i-gear" viewBox="0 0 12 12"><circle cx="6" cy="6" r="5"/><circle cx="6" cy="6" r="2" fill="#0a95ff"/></symbol>
  <symbol id="i-doc" viewBox="0 0 12 12"><path d="M2 0h6l3 3v9H2z"/></symbol>
  <symbol id="i-tree" viewBox="0 0 12 12"><rect x="4" y="0" width="4" height="4"/><rect x="0" y="7" width="4" height="4"/><rect x="8" y="7" width="4" height="4"/><rect x="4" y="7" width="4" height="4"/><rect x="5.5" y="4" width="1" height="3"/></symbol>
  <symbol id="i-bars" viewBox="0 0 12 12"><rect x="0" y="10.5" width="12" height="1.5"/><rect x="1.5" y="5" width="2" height="5"/><rect x="5" y="2" width="2" height="8"/><rect x="8.5" y="6" width="2" height="4"/></symbol>
  <symbol id="i-plus" viewBox="0 0 10 10"><circle cx="5" cy="5" r="5" fill="#fff"/><rect x="2.5" y="4.3" width="5" height="1.4" fill="#0a95ff"/><rect x="4.3" y="2.5" width="1.4" height="5" fill="#0a95ff"/></symbol>
</svg>

<div class="app-frame"></div>

<nav class="sidebar">
  <div class="brand"><span class="brand-mark"></span>Estatly</div>
  <ul class="nav">
    <li><svg class="ico"><use href="#i-gear"/></svg>Dashboard</li>
    <li><svg class="ico"><use href="#i-user"/></svg>Customers</li>
    <li><svg class="ico"><use href="#i-home"/></svg>Properties</li>
    <li><svg class="ico"><use href="#i-user"/></svg>Tenants</li>
    <li><svg class="ico"><use href="#i-sq"/></svg>Contacts</li>
    <li><svg class="ico"><use href="#i-gear"/></svg>Contractors</li>
    <li><svg class="ico"><use href="#i-user"/></svg>Employees</li>
    <li><svg class="ico"><use href="#i-doc"/></svg>Compliance Management</li>
    <li><svg class="ico"><use href="#i-gear"/></svg>Prevent. Maintenance<svg class="plus"><use href="#i-plus"/></svg></li>
    <li><svg class="ico"><use href="#i-tree"/></svg>Work Orders<svg class="plus"><use href="#i-plus"/></svg></li>
    <li><svg class="ico"><use href="#i-sq"/></svg>Purchase Orders</li>
    <li><svg class="ico"><use href="#i-gear"/></svg>Property Inspections<svg class="plus"><use href="#i-plus"/></svg></li>
    <li><svg class="ico"><use href="#i-bars"/></svg>Energy Management</li>
    <li><svg class="ico"><use href="#i-home"/></svg>Risk Management</li>
    <li><svg class="ico"><use href="#i-tree"/></svg>Project Management</li>
    <li><svg class="ico"><use href="#i-sq"/></svg>Financial - Budgeting</li>
    <li><svg class="ico"><use href="#i-user"/></svg>Tenant Requests</li>
    <li><svg class="ico"><use href="#i-doc"/></svg>Reports<svg class="plus"><use href="#i-plus"/></svg></li>
    <li><svg class="ico"><use href="#i-bars"/></svg>Visual Reports</li>
    <li><svg class="ico"><use href="#i-doc"/></svg>Files</li>
    <li><svg class="ico"><use href="#i-sq"/></svg>Pages<svg class="plus"><use href="#i-plus"/></svg></li>
    <li><svg class="ico"><use href="#i-gear"/></svg>Configurations<svg class="plus"><use href="#i-plus"/></svg></li>
    <li><svg class="ico"><use href="#i-gear"/></svg>Settings<svg class="plus"><use href="#i-plus"/></svg></li>
  </ul>
  <div class="collapse-btn"><svg width="11" height="10" viewBox="0 0 11 10"><path d="M5 0L0 5l5 5V6.5h6v-3H5z" fill="#fff"/></svg></div>
</nav>

<h1 class="main-title"><svg width="22" height="20" viewBox="0 0 12 12" fill="#2b2b2b"><use href="#i-home"/></svg>Active Dashboard</h1>

<div class="stat" style="left:552px;width:78px"><div class="ico-cell"><svg width="14" height="14" fill="#0094ff"><use href="#i-home"/></svg></div><div class="txt"><div class="lbl">Properties</div><div class="val">3</div></div></div>
<div class="stat" style="left:635px;width:69px"><div class="ico-cell"><svg width="14" height="14" fill="#0094ff"><use href="#i-user"/></svg></div><div class="txt"><div class="lbl">Tenants</div><div class="val">8</div></div></div>
<div class="stat" style="left:710px;width:146px"><div class="ico-cell"><svg width="13" height="13" viewBox="0 0 12 12" fill="#0094ff"><path d="M6 0l2 2.5H7V5h2.5V4L12 6 9.5 8V7H7v2.5h1L6 12 4 9.5h1V7H2.5v1L0 6l2.5-2v1H5V2.5H4z"/></svg></div><div class="txt"><div class="lbl">Total Properties Area</div><div class="val">422,000.00 sq.ft.</div></div></div>
<div class="stat" style="left:862px;width:146px"><div class="ico-cell"><svg width="13" height="13" viewBox="0 0 12 12" fill="#0094ff"><path d="M6 0l2 2.5H7V5h2.5V4L12 6 9.5 8V7H7v2.5h1L6 12 4 9.5h1V7H2.5v1L0 6l2.5-2v1H5V2.5H4z"/></svg></div><div class="txt"><div class="lbl">Rented Area</div><div class="val">233,500.00 sq.ft.</div></div></div>
<div class="stat" style="left:1013px;width:146px"><div class="ico-cell"><svg width="13" height="13" viewBox="0 0 12 12" fill="#0094ff"><path d="M6 0l2 2.5H7V5h2.5V4L12 6 9.5 8V7H7v2.5h1L6 12 4 9.5h1V7H2.5v1L0 6l2.5-2v1H5V2.5H4z"/></svg></div><div class="txt"><div class="lbl">Vacancies Area</div><div class="val">188,500.00 sq.ft.</div></div></div>

<div class="tabs">
  <div class="tab active"><svg viewBox="0 0 10 10"><circle cx="5" cy="5" r="4" fill="none" stroke="#fff" stroke-width="1.4"/><path d="M5 2.5V5h2" stroke="#fff" fill="none"/></svg>Last 7 days</div>
  <div class="tab"><svg viewBox="0 0 10 10"><circle cx="5" cy="5" r="4" fill="none" stroke="#fff" stroke-width="1.4"/><path d="M5 2.5V5h2" stroke="#fff" fill="none"/></svg>Last months</div>
  <div class="tab"><svg viewBox="0 0 10 10"><circle cx="5" cy="5" r="4" fill="none" stroke="#fff" stroke-width="1.4"/><path d="M5 2.5V5h2" stroke="#fff" fill="none"/></svg>Last 3 months</div>
  <div class="tab"><svg viewBox="0 0 10 10"><circle cx="5" cy="5" r="4" fill="none" stroke="#fff" stroke-width="1.4"/><path d="M5 2.5V5h2" stroke="#fff" fill="none"/></svg>Next 7 days</div>
  <div class="tab"><svg viewBox="0 0 10 10"><circle cx="5" cy="5" r="4" fill="none" stroke="#fff" stroke-width="1.4"/><path d="M5 2.5V5h2" stroke="#fff" fill="none"/></svg>Next months</div>
  <div class="tab"><svg viewBox="0 0 10 10"><circle cx="5" cy="5" r="4" fill="none" stroke="#fff" stroke-width="1.4"/><path d="M5 2.5V5h2" stroke="#fff" fill="none"/></svg>Next 3 months</div>
</div>

<section class="panel">
  <div class="range"><svg width="20" height="16" viewBox="0 0 12 12" fill="#2b2b2b"><use href="#i-bars"/></svg>12/27/2020 - 01/03/2021</div>
  <svg class="chart" width="903" height="815" viewBox="0 0 903 815">
    <defs><linearGradient id="arcGrad" x1="0" y1="0" x2="0" y2="1"><stop offset="0" stop-color="var(--arc-light)"/><stop offset="1" stop-color="#78b3ec"/></linearGradient></defs>
    <circle cx="287" cy="328" r="254" fill="none" stroke="var(--ring)" stroke-width="2"/>
    <path d="M287 74 A254 254 0 0 1 287 582" fill="none" stroke="url(#arcGrad)" stroke-width="28"/>
  </svg>
  <div class="date-pill">12/30/2020</div>
  <ul class="legend">
    <li style="color:var(--c-sched)"><span class="dot" style="background:var(--c-sched)"></span>Scheduled Maintenance</li>
    <li style="color:#5cc24a"><span class="dot" style="background:var(--c-done)"></span>Completed Scheduled Maintenance</li>
    <li style="color:var(--c-future)"><span class="dot" style="background:var(--c-future)"></span>Future Scheduled Maintenance</li>
    <li style="color:var(--c-wo)"><span class="dot" style="background:var(--c-wo)"></span>Scheduled Work Orders</li>
    <li style="color:var(--c-wodone)"><span class="dot" style="background:var(--c-wodone)"></span>Completed Work Orders</li>
    <li style="color:var(--c-insp)"><span class="dot" style="background:var(--c-insp)"></span>Property Inspections in Progress</li>
    <li style="color:#c4ad2e"><span class="dot" style="background:var(--c-inspdone)"></span>Completed Property Inspections</li>
  </ul>
</section>

<footer class="footer">Copyright © 2021 &nbsp;Estatly. &nbsp;All rights reserved.</footer>
</body>
</html>
```